Business Report Cover

We need a revamped quarterly report cover to send to our clients. We asset manage commercial and residential properties throughout the the United States. We use a .pdf version of a cover that we've used for years but would like a fresh updated look for 2018. The cover should include our company logo (KOV Enterprises) and a photo of the property as well as the Quarter/Year of the report.

```html
<!DOCTYPE html>
<html lang="en">
<head>
<meta charset="utf-8">
<title>Quarterly Operating Report – 1st Quarter 2018</title>
<link href="https://fonts.googleapis.com/css2?family=Dosis:wght@400;500;700&display=swap" rel="stylesheet">
<style>
  :root {
    --backdrop: #e9e6df;
    --paper: #ffffff;
    --ink: #111111;
    --brand-green: #0e763a;
    --soft-green: #7fbf9b;
    --font-main: "Dosis", "Arial Narrow", sans-serif;
  }
  * { box-sizing: border-box; margin: 0; padding: 0; }
  html, body {
    width: 1200px;
    height: 1200px;
    overflow: hidden;
    background: var(--backdrop);
  }
  .cover {
    position: absolute;
    left: 176px;
    top: 0;
    width: 847px;
    height: 1200px;
    background: var(--paper);
    font-family: var(--font-main);
    color: var(--ink);
  }
  .cover-art {
    position: absolute;
    inset: 0;
    width: 847px;
    height: 1200px;
  }
  .brand-name {
    position: absolute;
    left: 61px;
    top: 50px;
    font-size: 30px;
    font-weight: 700;
    letter-spacing: 0.5px;
    color: var(--ink);
  }
  .property-address {
    position: absolute;
    right: 36px;
    top: 36px;
    text-align: right;
    font-size: 20px;
    font-weight: 400;
    line-height: 26px;
  }
  .report-title {
    position: absolute;
    right: 45px;
    top: 952px;
    text-align: right;
  }
  .report-title .report-name,
  .report-title .report-quarter {
    display: block;
    font-size: 38px;
    font-weight: 500;
    line-height: 42px;
    letter-spacing: -0.5px;
  }
  .report-title .report-year {
    display: block;
    font-size: 88px;
    font-weight: 500;
    line-height: 96px;
    color: var(--brand-green);
    letter-spacing: -1px;
  }
</style>
</head>
<body>
  <main class="cover">
    <svg class="cover-art" viewBox="0 0 935 1323" preserveAspectRatio="none" aria-hidden="false">
      <defs>
        <linearGradient id="propertyTones" x1="0" y1="0" x2="0" y2="1">
          <stop offset="0" stop-color="#ffffff"/>
          <stop offset="0.18" stop-color="#dfe1e4"/>
          <stop offset="0.45" stop-color="#a9adb2"/>
          <stop offset="0.62" stop-color="#6f4038"/>
          <stop offset="0.8" stop-color="#55504b"/>
          <stop offset="1" stop-color="#3f413d"/>
        </linearGradient>
      </defs>
      <rect class="property-photo" x="0" y="230" width="935" height="800" fill="url(#propertyTones)"
            role="img" aria-label="Photo of the convenience store and fuel station property"/>
      <polygon class="paper-lower" points="0,1078 595,853 935,998 935,1323 0,1323" fill="#ffffff"/>
      <polygon class="band-left-dark" points="0,673 595,853 0,998" fill="var(--brand-green)"/>
      <polygon class="band-left-soft" points="0,998 595,853 0,1078" fill="var(--soft-green)"/>
      <polygon class="band-right-veil" points="935,723 595,853 935,767" fill="var(--brand-green)" opacity="0.35"/>
      <polygon class="band-right-dark" points="935,767 595,853 935,953" fill="var(--brand-green)"/>
      <polygon class="band-right-soft" points="935,953 595,853 935,998" fill="var(--soft-green)"/>
    </svg>

    <div class="brand-name">KOV Enterprises</div>

    <address class="property-address" style="font-style:normal">
      Riverton Corner Mart<br>
      4120 NE Harbor Point Dr.<br>
      Riverton, WA 98600
    </address>

    <h1 class="report-title">
      <span class="report-name">QUARTERLY OPERATING REPORT</span>
      <span class="report-quarter">1ST QUARTER</span>
      <span class="report-year">2018</span>
    </h1>
  </main>
</body>
</html>
```